Business Card for Vorla Parts Wholesale supplier

Hi There! I need a new business card for our company. We are specialized in selling Vorla parts, mostly we sell new LCD screens for Zelnar and Drelks. I would like to see that back in the design.

You can find the colors and logo's on our website: www.hartuvo.nl

Industry/Entity Type

Business

Contact Information for Business Card

My Details:
Tobias Lindqvist

Phone: 0031687203316
E-mail: Tobias@hartuvo.nl

Slogan: "Because Quality Matters"

Font styles to use
Sans Serif

Colors

Designer to choose colors to be used in the design.

Requirements
Must have
• A Black backside with the Hartuvo logo on it. The front side should be clean with only my contact details.
• But I'm also open for something really different or awesome!
Nice to have
• Remember that we are in the parts & repairing industry, So i'll be handing those business cards mainly to repair companies. Maybe you can do something with that thought :)

```html
<!DOCTYPE html>
<html lang="en">
<head>
<meta charset="utf-8">
<title>Hartuvo business card</title>
<link rel="stylesheet" href="https://fonts.googleapis.com/css2?family=Open+Sans:wght@400;600;700;800&display=swap">
<style>
  :root {
    --bg: #d9d6d2;
    --card-white: #fbfbfa;
    --card-black: #0d0d0d;
    --brand-orange: #f07a1e;
    --brand-orange-faint: #f7e3d4;
    --ink: #111111;
    --emboss: #1c1c1c;
    --emboss-edge: #2a2a2a;
  }
  * { margin: 0; padding: 0; box-sizing: border-box; }
  html, body { width: 1200px; height: 844px; overflow: hidden; }
  body {
    background: var(--bg);
    font-family: "Open Sans", Arial, sans-serif;
    position: relative;
  }
  .card {
    position: absolute;
    top: 261px;
    width: 500px;
    height: 322px;
    overflow: hidden;
    box-shadow: 0 6px 18px rgba(0,0,0,0.25);
  }
  .card--front { left: 70px; background: var(--card-white); }
  .card--back { left: 630px; background: var(--card-black); }

  .front-decoration {
    position: absolute;
    right: 30px;
    top: 70px;
    width: 170px;
    height: 170px;
    border-radius: 50%;
    background: var(--brand-orange-faint);
    opacity: 0.8;
  }
  .wordmark {
    position: absolute;
    left: 38px;
    top: 74px;
    display: flex;
    align-items: center;
    gap: 14px;
  }
  .wordmark__mark {
    width: 40px;
    height: 40px;
    background: var(--brand-orange);
  }
  .wordmark__name {
    font-weight: 800;
    font-size: 58px;
    line-height: 1;
    letter-spacing: 1px;
    color: var(--ink);
  }
  .contact {
    position: absolute;
    left: 40px;
    top: 186px;
    color: var(--ink);
  }
  .contact__name {
    color: var(--brand-orange);
    font-weight: 600;
    font-size: 17px;
    letter-spacing: 0.5px;
    text-transform: uppercase;
    margin-bottom: 4px;
  }
  .contact__line { font-size: 12.5px; line-height: 1.6; }
  .contact__label { color: var(--brand-orange); font-weight: 700; }
  .contact__sep { margin: 0 6px; }
  .contact__web {
    color: var(--brand-orange);
    font-weight: 700;
    font-size: 12.5px;
    line-height: 1.6;
  }
  .slogan {
    margin-top: 16px;
    font-size: 13.5px;
    font-weight: 600;
    text-transform: uppercase;
    letter-spacing: 0.3px;
  }

  .back-wordmark {
    position: absolute;
    inset: 0;
    display: flex;
    align-items: center;
    justify-content: center;
    gap: 16px;
  }
  .back-wordmark__mark {
    width: 44px;
    height: 44px;
    border-radius: 50%;
    background: var(--emboss);
  }
  .back-wordmark__name {
    font-weight: 800;
    font-size: 54px;
    letter-spacing: 1px;
    color: var(--emboss-edge);
  }
</style>
</head>
<body>
  <section class="card card--front" aria-label="Front of business card">
    <div class="front-decoration" aria-hidden="true"></div>
    <div class="wordmark">
      <span class="wordmark__mark" aria-hidden="true"></span>
      <span class="wordmark__name">hartuvo</span>
    </div>
    <div class="contact">
      <p class="contact__name">Tobias Lindqvist</p>
      <p class="contact__line">
        <span class="contact__label">P:</span> 0031687203316<span class="contact__sep">|</span><span class="contact__label">E:</span> Tobias@hartuvo.nl
      </p>
      <p class="contact__web">www.hartuvo.nl</p>
      <p class="slogan">Because Quality Matters</p>
    </div>
  </section>

  <section class="card card--back" aria-label="Back of business card">
    <div class="back-wordmark">
      <span class="back-wordmark__mark" aria-hidden="true"></span>
      <span class="back-wordmark__name">hartuvo</span>
    </div>
  </section>
</body>
</html>
```